Elevating our current Business Card Design

We want to elevate our current business card with a new design to look like a zenith 300 company. We are a premium lubricant distributor (oil and grease).
We need 2 versions, version 1 is as per the uploaded a copy of our current business card with the English version.
For our Chinese version we need to use the front to be English in English and have the back of the card designed exactly like the front for all info to be in Chinese.
The design template needs to be such that we can amend the template with adding different information for each person's card.
The background colour of the card can be changed- we just need to clearly see all information on the card and logos.
The QJR and Ember steady logos cannot have any colour or display changes- only use the logos attached.
All logos need to be included and all information from the attached current card

```html
<!DOCTYPE html>
<html lang="en">
<head>
<meta charset="utf-8">
<title>Orvane Business Card</title>
<link rel="stylesheet" href="https://fonts.googleapis.com/css2?family=Open+Sans:wght@400;600;700&family=Ubuntu:wght@500&display=swap">
<style>
  :root {
    --stage: #2a2a2a;
    --gold: #d39e2a;
    --gold-light: #e4b43a;
    --red: #e32b26;
    --green: #06301f;
    --white: #ffffff;
    --placeholder: #d6d6d6;
  }
  * { box-sizing: border-box; margin: 0; padding: 0; }
  html, body { width: 1200px; height: 780px; overflow: hidden; }
  body {
    background: var(--stage);
    font-family: "Open Sans", sans-serif;
    display: flex;
    align-items: center;
    justify-content: center;
    gap: 40px;
  }
  .card {
    width: 560px;
    height: 320px;
    position: relative;
    overflow: hidden;
    box-shadow: 0 10px 30px rgba(0,0,0,.45);
  }

  /* Front */
  .card-front {
    background: var(--gold);
    display: flex;
    align-items: center;
    justify-content: center;
  }
  .front-pattern {
    position: absolute;
    inset: 0;
    background: radial-gradient(circle at 50% 45%, var(--gold-light), var(--gold) 75%);
  }
  .front-brand {
    position: relative;
    display: flex;
    align-items: center;
    gap: 18px;
  }
  .brand-dot {
    width: 44px;
    height: 44px;
    border-radius: 50%;
    background: var(--white);
  }
  .brand-name {
    font-family: "Ubuntu", sans-serif;
    font-weight: 500;
    font-size: 78px;
    color: var(--red);
    letter-spacing: 1px;
  }

  /* Back */
  .card-back {
    background: var(--green);
    display: flex;
  }
  .partner-strip {
    width: 165px;
    background: var(--white);
    display: flex;
    gap: 10px;
    padding: 16px 14px 16px 18px;
  }
  .brand-block {
    width: 74px;
    border: 1.5px solid var(--red);
    border-radius: 8px;
    overflow: hidden;
    display: flex;
    flex-direction: column;
    margin-top: 8px;
  }
  .company-part {
    flex: 1;
    display: flex;
    justify-content: center;
    align-items: center;
    gap: 4px;
    writing-mode: vertical-rl;
    padding: 8px 4px;
  }
  .company-name {
    font-weight: 700;
    font-size: 20px;
    color: var(--red);
    line-height: 1;
  }
  .company-tag {
    font-size: 8px;
    color: var(--red);
    line-height: 1.2;
  }
  .supplier-part {
    height: 130px;
    background: var(--red);
    display: flex;
    justify-content: center;
    align-items: center;
    gap: 4px;
    writing-mode: vertical-rl;
    padding: 8px 4px;
  }
  .supplier-name {
    font-weight: 700;
    font-size: 16px;
    color: var(--white);
    line-height: 1;
  }
  .supplier-tag {
    font-size: 8px;
    color: var(--white);
    line-height: 1.2;
  }
  .partner-column {
    flex: 1;
    display: flex;
    flex-direction: column;
    align-items: center;
    justify-content: space-between;
  }
  .partner-name {
    writing-mode: vertical-rl;
    font-weight: 700;
    font-size: 14px;
    color: var(--green);
    line-height: 1;
  }
  .cert-badge {
    width: 36px;
    height: 36px;
    border-radius: 50%;
    background: var(--placeholder);
  }

  .contact-panel {
    flex: 1;
    position: relative;
    padding: 44px 42px 0 0;
    text-align: right;
    color: var(--white);
  }
  .accent-bar {
    position: absolute;
    right: 0;
    top: 40px;
    width: 22px;
    height: 52px;
    background: var(--red);
  }
  .person-name {
    font-family: "Ubuntu", sans-serif;
    font-weight: 500;
    font-size: 30px;
    color: var(--red);
    line-height: 1.05;
  }
  .person-role {
    font-weight: 600;
    font-size: 14px;
    margin-bottom: 14px;
  }
  .address {
    font-size: 13.5px;
    line-height: 1.35;
    margin-bottom: 12px;
  }
  .contact-list { list-style: none; }
  .contact-list li {
    display: flex;
    justify-content: flex-end;
    align-items: center;
    gap: 8px;
    font-size: 13.5px;
    line-height: 1.55;
  }
  .contact-icon {
    width: 13px;
    height: 13px;
    flex-shrink: 0;
    fill: none;
    stroke: var(--red);
    stroke-width: 2;
  }
</style>
</head>
<body>

<section class="card card-front">
  <div class="front-pattern" role="img" aria-label="Repeating gold foil brand pattern"></div>
  <div class="front-brand">
    <span class="brand-dot"></span>
    <span class="brand-name">Orvane</span>
  </div>
</section>

<section class="card card-back">
  <aside class="partner-strip">
    <div class="brand-block">
      <div class="company-part">
        <span class="company-name">Orvane</span>
        <span class="company-tag">Orvane Lubricant<br>Partners</span>
      </div>
      <div class="supplier-part">
        <span class="supplier-name">Kestrel</span>
        <span class="supplier-tag">Premium Oils</span>
      </div>
    </div>
    <div class="partner-column">
      <span class="partner-name">Ember steady</span>
      <span class="cert-badge" role="img" aria-label="QJR certificate placeholder"></span>
      <span class="cert-badge" role="img" aria-label="QJR certificate placeholder"></span>
      <span class="cert-badge" role="img" aria-label="QJR certificate placeholder"></span>
    </div>
  </aside>

  <div class="contact-panel">
    <span class="accent-bar"></span>
    <h1 class="person-name">Marina Holloway</h1>
    <p class="person-role">Administration Executive</p>
    <p class="address">48 Freight Parade<br>Belmont, WA 6104</p>
    <ul class="contact-list">
      <li>1300 472 816
        <svg class="contact-icon" viewBox="0 0 16 16"><path d="M3 2l3 1 1 3-2 1.5a9 9 0 0 0 4 4L10.5 9.5l3 1 .5 3-2 1.5C6 14 2 10 1.5 4z"/></svg>
      </li>
      <li>+61 412 907 364
        <svg class="contact-icon" viewBox="0 0 16 16"><rect x="4" y="1.5" width="8" height="13" rx="1.5"/></svg>
      </li>
      <li>+61 8 9250 4417
        <svg class="contact-icon" viewBox="0 0 16 16"><rect x="2" y="6" width="12" height="8" rx="1"/><path d="M5 6V2h6v4"/></svg>
      </li>
      <li>www.orvanedirect.com
        <svg class="contact-icon" viewBox="0 0 16 16"><circle cx="8" cy="8" r="6.5"/><path d="M1.5 8h13M8 1.5c3 3.5 3 9.5 0 13M8 1.5c-3 3.5-3 9.5 0 13"/></svg>
      </li>
      <li>marina.holloway@orvanedirect.com
        <svg class="contact-icon" viewBox="0 0 16 16"><rect x="1.5" y="3.5" width="13" height="9" rx="1"/><path d="M1.5 4l6.5 5 6.5-5"/></svg>
      </li>
    </ul>
  </div>
</section>

</body>
</html>
```